Residential real estate home builder in west texas

We need a website design for our home building business based in west Texas called Birch Hollow homes. We build new construction for potential homeowners in Amarillo. Currently we do not have any completed construction, but we have floor plans and architectural drawings of the front elevation. The website would need to be able to properly advertise a architectural drawing, floor plans, and descriptive content at the initial phase. The website will need to be simple but professional with generic picture content.
The website will need the ability to be updated in the future for the additions of home pictures, and video content and virtual tours of the homes.

Target Market(s)

Potential Home buyers

Industry/Entity Type

Real Estate

Number of Pages Required

5+ page

Font styles to use
Sans Serif

Colors
f37122
757575

Requirements
Must have
• Web design must be simple and easy to navigate. There is not much picture content, so it will need to be simple.
• 5 pages:
• Home, Available homes, Available floor plans, guide to ownership, Contact
• The website will need the ability to be updated in the future for the additions of pictures, and video content of the homes when they are built. ( A virtual tour).
Nice to have
• I would like to see a modern and cohesive design. Contact information at the bottom of each page.
Should not have
• A Black background

```html
<!DOCTYPE html>
<html lang="en">
<head>
<meta charset="utf-8">
<title>Birch Hollow Homes</title>
<link rel="stylesheet" href="https://fonts.googleapis.com/css2?family=Mulish:wght@400;600;700&family=Open+Sans:wght@400;600&display=swap">
<style>
:root{
  --orange:#f37122;
  --orange-deep:#e4581f;
  --rust:#9c6a5c;
  --gray:#757575;
  --gray-dark:#555;
  --gray-light:#e6e6e6;
  --text:#4a4a55;
  --white:#fff;
}
*{margin:0;padding:0;box-sizing:border-box}
html,body{width:1200px;height:2862px;overflow:hidden}
body{font-family:"Open Sans",sans-serif;color:var(--text);background:var(--white);position:relative}
.abs{position:absolute}
.heading{font-family:"Mulish",sans-serif;font-weight:400;text-transform:uppercase}

/* header */
.site-header{top:0;left:0;width:1200px;height:115px;background:var(--white)}
.brand{left:95px;top:40px;display:flex;align-items:center;gap:10px;font-family:"Mulish",sans-serif;font-weight:600;font-size:23px;line-height:30px;color:var(--gray-dark);letter-spacing:.5px;white-space:nowrap}
.brand-mark{width:18px;height:18px;background:var(--orange)}
.main-nav{top:48px;right:92px;display:flex;gap:28px;font-family:"Mulish",sans-serif;font-size:18px;line-height:24px;color:var(--gray-dark);white-space:nowrap}
.main-nav .active{color:var(--orange)}

/* hero */
.hero{top:115px;left:0;width:1200px;height:568px}
.hero-photo{position:absolute;inset:0;background:linear-gradient(180deg,#6f9fd0 0%,#b9d2ea 35%,#e9eef0 55%,#8a8f86 78%,#4e6b3c 100%)}
.hero-title{left:108px;top:180px;font-size:44px;line-height:52px;color:var(--white);letter-spacing:1px}
.hero-btn{left:110px;top:308px;width:166px;height:44px;background:rgba(70,70,70,.7);color:var(--white);font-size:15px;display:flex;align-items:center;justify-content:center;text-transform:uppercase}
.dots{left:555px;top:528px;display:flex;gap:10px}
.dots span{width:13px;height:13px;border-radius:50%;background:var(--white)}
.dots span:first-child{background:transparent;border:2px solid var(--white)}

/* welcome */
.welcome{top:683px;left:0;width:1200px;height:378px;background:linear-gradient(180deg,var(--rust) 0%,#c3603a 55%,var(--orange-deep) 100%);color:var(--white);text-align:center}
.welcome h1{margin-top:68px;font-size:34px;letter-spacing:1px}
.rule{width:80px;height:3px;background:currentColor;margin:10px auto 0}
.welcome p{width:900px;margin:24px auto 0;font-size:14px;line-height:21px}
.welcome p+p{margin-top:14px}
.outline-btn{display:inline-flex;align-items:center;justify-content:center;border:2px solid currentColor;text-transform:uppercase;font-size:15px}
.welcome .outline-btn{margin-top:30px;width:180px;height:44px}

/* floor plans */
.floor-plans{top:1061px;left:0;width:1200px;height:515px;background:#ededed}
.floor-photo{position:absolute;left:0;top:0;width:720px;height:515px;background:linear-gradient(90deg,#cfcfcf 0%,#e4e2de 60%,rgba(237,237,237,0) 100%)}
.notch{position:absolute;left:0;top:-1px}
.floor-copy{left:628px;top:118px;width:480px}
.floor-copy h2{font-size:34px;color:var(--gray-dark)}
.floor-copy p{font-size:14px;line-height:21px;margin-top:14px;color:var(--gray-dark)}
.gray-btn{position:absolute;left:2px;top:227px;width:168px;height:46px;background:linear-gradient(180deg,#8a8a8a,#5a5a5a);color:var(--white);font-size:15px;display:flex;align-items:center;justify-content:center;text-transform:uppercase}

/* architectural */
.arch{top:1576px;left:0;width:1200px;height:431px;background:var(--white)}
.arch h2{position:absolute;top:62px;width:100%;text-align:center;font-size:32px;color:var(--orange)}
.tours{top:2007px;left:0;width:1200px;height:493px;background:var(--gray-light)}
.card{top:1710px;width:312px;height:347px;background:var(--white);border:1px solid #d6d6d6}
.card-img{height:190px;border-bottom:1px solid #d6d6d6}
.card-img.blue{background:linear-gradient(135deg,#e8f0fa,#c9dbef)}
.card-img.desk{background:linear-gradient(135deg,#cfd6dc,#9ab2c8)}
.card-img.sketch{background:linear-gradient(135deg,#f4f4f4,#d9d9d9)}
.card h3{font-family:"Mulish",sans-serif;font-weight:600;font-size:18px;margin:20px 0 0 32px;color:#333}
.card p{font-size:12.5px;line-height:20px;margin:8px 30px 0 32px;color:var(--gray)}
.card .more{display:block;margin:10px 0 0 32px;font-size:12.5px;color:var(--orange);text-transform:uppercase}
.arrow{top:1852px}

.tours h2{position:absolute;left:99px;top:165px;font-size:28px;line-height:34px;color:var(--gray-dark)}
.tours p{position:absolute;left:99px;top:245px;width:260px;font-size:12.5px;line-height:25px;color:var(--gray-dark)}
.tours .outline-btn{position:absolute;left:103px;top:365px;width:147px;height:34px;color:var(--orange);font-size:13px}
.video{top:2171px;height:233px;border:4px solid var(--white)}
.video.exterior{left:391px;width:340px;background:linear-gradient(180deg,#3d5270 0%,#6b7a8e 55%,#4c5e3a 100%)}
.video.interior{left:759px;width:342px;background:linear-gradient(135deg,#e9ecee 0%,#b9a18a 55%,#7a3e1c 100%)}
.play{position:absolute;left:50%;top:50%;width:58px;height:58px;margin:-29px 0 0 -29px}

/* footer */
.site-footer{top:2500px;left:0;width:1200px;height:301px;background:var(--gray);color:var(--white)}
.col{top:74px}
.col h4{font-family:"Mulish",sans-serif;font-weight:600;font-size:17px;text-transform:uppercase;margin-bottom:14px}
.col li{list-style:none;font-size:13.5px;line-height:30px;white-space:nowrap}
.contact li{display:flex;align-items:center;gap:8px}
.social{display:flex;gap:8px}
.social span{width:36px;height:36px;border:2px solid var(--white);border-radius:50%}
.copyright{top:2801px;left:0;width:1200px;height:61px;background:var(--orange-deep);color:var(--white);font-size:12.5px;display:flex;align-items:center;justify-content:center}
</style>
</head>
<body>

<header class="site-header abs">
  <div class="brand abs"><span class="brand-mark"></span>Birch Hollow Homes</div>
  <nav class="main-nav abs">
    <span class="active">Home</span><span>Available homes</span><span>Available floor plans</span><span>Guide to ownership</span><span>Contact</span>
  </nav>
</header>

<section class="hero abs">
  <div class="hero-photo" role="img" aria-label="Modern white two-storey home with garden under a blue sky"></div>
  <h1 class="hero-title heading abs">Home construction<br>&amp; floor plans</h1>
  <a class="hero-btn abs">View homes</a>
  <div class="dots abs"><span></span><span></span><span></span><span></span></div>
</section>

<section class="welcome abs">
  <h1 class="heading">Welcome to Birch Hollow Homes</h1>
  <div class="rule"></div>
  <p>facilisis volutpat in imperdiet sit amet sem Aliquam nec erat at purus cursus interdum Vestibulum ligula augue bibendum accumsan vestibulum ut commodo a mi Morbi ornare gravida elit Integer congue augue et malesuada iaculis ipsum dui aliquet felis at cursus magna nisl nec elit Donec iaculis diam a nisi accumsan viverra Duis sed tellus</p>
  <p>et tortor vestibulum gravida Praesent elementum elit at tellus Curabitur metus ipsum luctus eu malesuada ut tincidunt sed diam Donec quis mi sed magna hendrerit accumsan Suspendisse risus nibh ultricies</p>
  <a class="outline-btn">Read more</a>
</section>

<section class="floor-plans abs">
  <div class="floor-photo" role="img" aria-label="Hands drafting a floor plan with ruler, pencil and coffee mug"></div>
  <svg class="notch" width="1200" height="32" viewBox="0 0 1200 32"><polygon points="430,0 763,0 700,30 493,30" fill="#e4581f"/></svg>
  <div class="floor-copy abs">
    <h2 class="heading">Floor plans</h2>
    <p>ullamcorper est eget tempor cursus neque mi consectetuer mi a ultricies massa est sed nisl Class aptent taciti sociosqu ad</p>
    <p>conubia nostra per inceptos hymenaeos Proin nulla arcu nonummy luctus dictum eget fermentum et lorem ipsum cligula augue bibendum accumsan vestibulum ut commodo a mi Morbi ornare gravida elit Integer congue augue et malesuada iaculis ipsum dui</p>
    <a class="gray-btn">Read more</a>
  </div>
</section>

<section class="arch abs">
  <h2 class="heading">Architectural drawing</h2>
  <div class="rule abs" style="left:560px;top:108px;color:var(--orange)"></div>
</section>
<section class="tours abs">
  <h2 class="heading">Virtual tours of<br>the homes</h2>
  <p>Proesent elementum elit at tellus nec ultricies sit amet porttitor mattis Anterdum nec interdum vel blandit sed nulla In ullamcorper est eget tem</p>
  <a class="outline-btn">View more</a>
</section>

<svg class="arrow abs" style="left:74px" width="26" height="62" viewBox="0 0 26 62"><polyline points="24,2 2,31 24,60" fill="none" stroke="#777" stroke-width="2"/></svg>
<svg class="arrow abs" style="left:1098px" width="26" height="62" viewBox="0 0 26 62"><polyline points="2,2 24,31 2,60" fill="none" stroke="#777" stroke-width="2"/></svg>

<article class="card abs" style="left:114px">
  <div class="card-img blue" role="img" aria-label="Blue technical floor plan drawing"></div>
  <h3>Your Tittle goes here</h3>
  <p>Class aptent taciti sociosqu ad litora torquent per conubia nostra per inceptos hymenaeos Proin nulla arcu</p>
  <a class="more">Read more</a>
</article>
<article class="card abs" style="left:442px">
  <div class="card-img desk" role="img" aria-label="Architect working on blueprints at a desk"></div>
  <h3>Your Tittle goes here</h3>
  <p>Class aptent taciti sociosqu ad litora torquent per conubia nostra per inceptos hymenaeos Proin nulla arcu</p>
  <a class="more">Read more</a>
</article>
<article class="card abs" style="left:768px">
  <div class="card-img sketch" role="img" aria-label="Pencil sketch of a house elevation"></div>
  <h3>Your Tittle goes here</h3>
  <p>Class aptent taciti sociosqu ad litora torquent per conubia nostra per inceptos hymenaeos Proin nulla arcu</p>
  <a class="more">Read more</a>
</article>

<div class="video exterior abs" role="img" aria-label="Video tour of a home exterior at dusk">
  <svg class="play" viewBox="0 0 58 58"><circle cx="29" cy="29" r="27" fill="rgba(0,0,0,.15)" stroke="#fff" stroke-width="3"/><polygon points="23,17 41,29 23,41" fill="#fff"/></svg>
</div>
<div class="video interior abs" role="img" aria-label="Video tour of a bright open-plan interior">
  <svg class="play" viewBox="0 0 58 58"><circle cx="29" cy="29" r="27" fill="rgba(0,0,0,.15)" stroke="#fff" stroke-width="3"/><polygon points="23,17 41,29 23,41" fill="#fff"/></svg>
</div>

<footer class="site-footer abs">
  <div class="col abs" style="left:88px"><h4>Company</h4><ul><li>Home</li><li>Available homes</li><li>Available floor plans</li><li>Guide to ownership</li></ul></div>
  <div class="col abs" style="left:279px"><h4>Resources</h4><ul><li>Help</li><li>FAQ</li><li>Sitemap</li><li>Term of Use</li></ul></div>
  <div class="col abs" style="left:450px"><h4>Support</h4><ul><li>Support</li><li>News &amp; Blogs</li><li>Clients</li><li>Contcat Us</li></ul></div>
  <div class="col contact abs" style="left:612px"><h4>Contact us</h4><ul>
    <li><svg width="12" height="16" viewBox="0 0 12 16"><path d="M6 0a6 6 0 0 0-6 6c0 4 6 10 6 10s6-6 6-10a6 6 0 0 0-6-6zm0 8.5A2.5 2.5 0 1 1 6 3.5a2.5 2.5 0 0 1 0 5z" fill="#fff"/></svg>418 Prairie Bend Rd Amarillo TX 79101</li>
    <li><svg width="14" height="14" viewBox="0 0 14 14"><path d="M3 1l2 3-1.5 1.5a8 8 0 0 0 5 5L10 9l3 2-1 2.5C6 13.5.5 8 .5 2z" fill="none" stroke="#fff" stroke-width="1.2"/></svg>806.555.0147</li>
    <li><svg width="15" height="11" viewBox="0 0 15 11"><rect x=".6" y=".6" width="13.8" height="9.8" fill="none" stroke="#fff" stroke-width="1.2"/><polyline points=".6,.6 7.5,6 14.4,.6" fill="none" stroke="#fff" stroke-width="1.2"/></svg>hello@birchhollowhomes.com</li>
  </ul></div>
  <div class="col abs" style="left:925px"><h4>Follow us</h4><div class="social"><span></span><span></span><span></span><span></span></div></div>
</footer>
<div class="copyright abs">© 2017 Company Name &nbsp;All right reserved</div>

</body>
</html>
```